Stationery Design Project

We need a stationery design for our Norwegian trucking company. We have existed for about 15 years and our 12 drivers uses relatively new vehicles to transport goods around in northern Norway. Long distance routes with fresh fish og food transport is our main operations.

We have already made alogo that's printed on our trucks. The logo and a picture of our trucks is attached. I think the logo i crappy, but since its already in use, changing it is not an option in this round. Still using a better colour scheme in the overall stationery and more interesting fonts is possible (altso in the logo).

Company details:
Name: Kjelvraket AS
Organisation nr 873 615 309
Post adress: 8642 Raudvik

I like minimalism and simplicity. I am avalibly for questions in normal GMT working hours either here or on mail: ivar@fjordlast.no

Reason: Hi. Im extending the deadline because I needed some time to find a vector file of our logo. Sorry for the inconvenience

Hi, and thanks for all your interest in the project. Some updates:

-          I have decided to commit to using one of the designs. Some designer will get the payment.

-          I have extended the deadline with 24 hours since I needed some time to find our firms vector logo (a slow Swedish man was holding me up)

-          We will not choose a design before the deadline. No need to rush.

-          We have received a lot of great design and think there is a need to specified the product we want to make:

o   Business Card for all our employers. I just need the design and will duplicate with the correct numbers and name myself. The information on should be: Logo, employer’s name, Phone number, email, website, Postal number and address. Use this as a template: logo, Leif Brattvoll, 47382066, Leif@fjordlast.no,, fjordlast.no, 8642 Raudvik. The order and placement of the information is your creative decision.

o   Stickers to put on the goods we travel. On the sticker the should be the following information: Logo, phone number, Tekst and link: Fraktæ av Kjelvraket. Ke du syns? Fjordlast.no/tilbakemelding (this means: Handled by Kjelvraket. What do you think Fjordlast.no/feedback -à the link will be a feedback form). The placement the information and size is your creative decision with some stings: we have been thinking of using Drukko for printing and see that a size about 6x6 cm, 8x5 or something like that. (with 3000 copies our budget is 200 punds). Any suggestions of other suppliers are welcome. Drukko price calculator http://www.drukkolabelhouse.co.uk/digital-litho-printing/printing-labels-tags/stickers/

o   Letterhead with logo, address, phone number and organizational number.

o   Envelopes with logo,address, phone number and organizational number.

Have a nice day.

 

 

• Using the blue colour in the logo and using a similar graphic approch.

```html
<!DOCTYPE html>
<html lang="no">
<head>
<meta charset="utf-8">
<title>Kjelvraket AS – Stationery</title>
<link href="https://fonts.googleapis.com/css2?family=Source+Sans+3:wght@400;600;700&family=Great+Vibes&display=swap" rel="stylesheet">
<style>
  :root {
    --navy: #0c2f80;
    --blue: #1a7ed6;
    --red: #e2202c;
    --ink: #555a60;
    --paper: #ffffff;
    --backdrop: #e9eaeb;
  }
  * { box-sizing: border-box; margin: 0; padding: 0; }
  html, body { width: 1200px; height: 903px; overflow: hidden; }
  body {
    position: relative;
    background: radial-gradient(ellipse at 50% 40%, #f7f7f7 0%, var(--backdrop) 100%);
    font-family: "Source Sans 3", "Helvetica Neue", Arial, sans-serif;
  }
  .sheet {
    position: absolute;
    background: var(--paper);
    box-shadow: 0 1px 5px rgba(0,0,0,.28);
    overflow: hidden;
  }
  .wordmark {
    position: absolute;
    color: var(--navy);
    font-weight: 700;
    letter-spacing: .5px;
    white-space: nowrap;
    line-height: 1;
  }
  .band {
    position: absolute;
    display: flex;
    align-items: center;
    color: #fff;
    white-space: nowrap;
  }
  .band--navy { background: var(--navy); }
  .band--red { background: var(--red); }
  .item { position: absolute; display: flex; align-items: center; gap: 5px; }
  .item svg { fill: #fff; flex: none; }

  /* Letterhead */
  .letterhead { left: 290px; top: 12px; width: 620px; height: 876px; z-index: 1; }
  .letterhead .wordmark { left: 42px; top: 62px; font-size: 46px; }
  .letter-body {
    position: absolute; left: 73px; top: 196px; width: 500px;
    color: var(--ink); font-size: 12px; line-height: 16.8px;
  }
  .letter-body .salutation { font-weight: 700; margin-bottom: 16px; }
  .letter-body p { margin-bottom: 16px; }
  .signature {
    position: absolute; left: 76px; top: 648px;
    font-family: "Great Vibes", cursive; font-size: 34px; color: #222;
  }
  .signer-title { position: absolute; left: 75px; top: 688px; font-size: 12px; font-weight: 700; color: var(--ink); }
  .letterhead .band--navy { left: 0; top: 825px; width: 450px; height: 16px; clip-path: polygon(0 0,100% 0,95% 100%,0 100%); font-size: 11px; }
  .letterhead .band--red { left: 425px; top: 831px; width: 195px; height: 16px; clip-path: polygon(7% 0,100% 0,100% 100%,0 100%); font-size: 10px; }

  /* Business cards */
  .card { width: 266px; height: 150px; z-index: 3; }
  .card--front { left: 77px; top: 440px; }
  .card--front .wordmark { left: 0; right: 0; text-align: center; top: 55px; font-size: 30px; }
  .card--front .band--red { left: 0; top: 127px; width: 100%; height: 10px; justify-content: center; font-size: 7px; gap: 4px; }
  .card--back { left: 77px; top: 635px; }
  .card--back .wordmark { left: 12px; top: 20px; font-size: 30px; }
  .card-name { position: absolute; left: 51px; top: 90px; color: var(--navy); font-size: 12px; letter-spacing: .3px; }
  .card--back .band--navy { left: 0; top: 121px; width: 176px; height: 11px; clip-path: polygon(0 0,100% 0,96% 100%,0 100%); font-size: 7px; }
  .card--back .band--red { left: 169px; top: 126px; width: 97px; height: 10px; clip-path: polygon(6% 0,100% 0,100% 100%,0 100%); font-size: 7px; }

  /* Envelope */
  .envelope { left: 525px; top: 432px; width: 651px; height: 325px; z-index: 2; }
  .envelope .wordmark { left: 30px; top: 36px; font-size: 34px; }
  .envelope .band--navy { left: 0; top: 285px; width: 465px; height: 16px; clip-path: polygon(0 0,100% 0,95% 100%,0 100%); font-size: 11px; }
  .envelope .band--red { left: 440px; top: 291px; width: 211px; height: 16px; clip-path: polygon(7% 0,100% 0,100% 100%,0 100%); font-size: 10px; }

  /* Sticker */
  .sticker {
    position: absolute; left: 934px; top: 124px; width: 184px; height: 184px;
    border-radius: 50%; border: 3px solid var(--navy); background: var(--paper);
    overflow: hidden; box-shadow: 0 1px 5px rgba(0,0,0,.28); z-index: 1;
  }
  .sticker .wordmark { left: 0; right: 0; text-align: center; top: 40px; font-size: 21px; }
  .sticker-text { position: absolute; left: 0; right: 0; text-align: center; color: #222; }
  .sticker-line1 { top: 80px; font-size: 10.5px; }
  .sticker-line2 { top: 94px; font-size: 12px; letter-spacing: .3px; }
  .sticker .band--red { left: 4px; top: 109px; width: 168px; height: 14px; clip-path: polygon(0 0,100% 0,96% 100%,0 100%); justify-content: center; font-size: 10.5px; }
  .sticker .band--navy { left: 50px; top: 142px; width: 120px; height: 13px; clip-path: polygon(5% 0,100% 0,100% 100%,0 100%); font-size: 10px; }
</style>
</head>
<body>

<svg width="0" height="0" style="position:absolute">
  <defs>
    <symbol id="icon-phone" viewBox="0 0 10 10"><rect x="0.5" y="1" width="9" height="8" rx="1"/><rect x="2" y="2.5" width="2" height="5" fill="#0c2f80"/><rect x="5" y="2.5" width="3" height="1" fill="#0c2f80"/><rect x="5" y="4.5" width="3" height="1" fill="#0c2f80"/><rect x="5" y="6.5" width="3" height="1" fill="#0c2f80"/></symbol>
    <symbol id="icon-pin" viewBox="0 0 10 10"><path d="M5 0.5a3.3 3.3 0 0 0-3.3 3.3C1.7 6.3 5 9.5 5 9.5s3.3-3.2 3.3-5.7A3.3 3.3 0 0 0 5 0.5zm0 4.6a1.3 1.3 0 1 1 0-2.6 1.3 1.3 0 0 1 0 2.6z"/></symbol>
    <symbol id="icon-globe" viewBox="0 0 10 10"><circle cx="5" cy="5" r="4.5"/><path d="M5 0.5v9M0.5 5h9M5 0.5c-2.2 2.5-2.2 6.5 0 9M5 0.5c2.2 2.5 2.2 6.5 0 9" stroke="#e2202c" stroke-width="0.7" fill="none"/></symbol>
    <symbol id="icon-mail" viewBox="0 0 10 10"><rect x="0.5" y="2" width="9" height="6" rx="0.8"/><path d="M0.8 2.4L5 5.6l4.2-3.2" stroke="#0c2f80" stroke-width="0.8" fill="none"/></symbol>
  </defs>
</svg>

<!-- Letterhead -->
<section class="sheet letterhead">
  <div class="wordmark">Kjelvraket</div>
  <div class="letter-body">
    <p class="salutation">Lorem Ipsum,</p>
    <p>Cras mattis consectetur purus sit amet fermentum. Etiam porta sem malesuada magna mollis euismod. Integer posuere erat a ante venenatis dapibus posuere velit aliquet. Cras justo odio, dapibus ac facilisis in, egestas eget quam. Aenean eu leo quam. Pellentesque ornare sem lacinia quam venenatis vestibulum.</p>
    <p>Vivamus sagittis lacus vel augue laoreet rutrum faucibus dolor auctor. Donec sed odio dui. Etiam porta sem malesuada magna mollis euismod. Morbi leo risus, porta ac consectetur ac, vestibulum at eros. Nullam id dolor id nibh ultricies vehicula ut id elit.</p>
    <p>Donec id elit non mi porta gravida at eget metus. Fusce dapibus, tellus ac cursus commodo, tortor mauris condimentum nibh, ut fermentum massa justo sit amet risus. Cras justo odio, dapibus ac facilisis in, egestas eget quam. Cum sociis natoque penatibus et magnis dis parturient montes, nascetur ridiculus mus.</p>
    <p>Cum sociis natoque penatibus et magnis dis parturient montes, nascetur ridiculus mus. Donec ullamcorper nulla non metus auctor fringilla. Aenean lacinia bibendum nulla sed consectetur. Sed posuere consectetur est at lobortis. Duis mollis, est non commodo luctus, nisi erat porttitor ligula, eget lacinia odio sem nec elit. Nullam quis risus eget urna mollis ornare vel eu leo, blandit tempus porttitor. Aenean lacinia bibendum nulla sed consectetur, sit amet, consectetur adipiscing elit.</p>
    <p>Cras justo odio, dapibus ac facilisis in, egestas eget quam. Morbi leo risus, porta ac consectetur ac, vestibulum at eros. Duis mollis, est non commodo luctus, nisi erat porttitor ligula, eget lacinia odio sem nec elit. Integer posuere erat a ante venenatis dapibus posuere velit aliquet. Vivamus sagittis lacus vel augue laoreet rutrum faucibus dolor auctor.</p>
  </div>
  <div class="signature">Your Name</div>
  <div class="signer-title">Company Director</div>
  <div class="band band--navy">
    <span class="item" style="left:90px"><svg width="9" height="9"><use href="#icon-phone"/></svg>873 615 309</span>
    <span class="item" style="left:276px"><svg width="9" height="9"><use href="#icon-pin"/></svg>8642 Raudvik</span>
  </div>
  <div class="band band--red">
    <span class="item" style="left:50px"><svg width="9" height="9"><use href="#icon-globe"/></svg>www.fjordlast.no</span>
  </div>
</section>

<!-- Envelope -->
<section class="sheet envelope">
  <div class="wordmark">Kjelvraket</div>
  <div class="band band--navy">
    <span class="item" style="left:105px"><svg width="9" height="9"><use href="#icon-phone"/></svg>873 615 309</span>
    <span class="item" style="left:291px"><svg width="9" height="9"><use href="#icon-pin"/></svg>8642 Raudvik</span>
  </div>
  <div class="band band--red">
    <span class="item" style="left:51px"><svg width="9" height="9"><use href="#icon-globe"/></svg>www.fjordlast.no</span>
  </div>
</section>

<!-- Business card front -->
<section class="sheet card card--front">
  <div class="wordmark">Kjelvraket</div>
  <div class="band band--red"><svg width="7" height="7"><use href="#icon-globe"/></svg>www.fjordlast.no</div>
</section>

<!-- Business card back -->
<section class="sheet card card--back">
  <div class="wordmark">Kjelvraket</div>
  <div class="card-name">LEIF BRATTVOLL</div>
  <div class="band band--navy">
    <span class="item" style="left:16px;gap:4px"><svg width="7" height="7"><use href="#icon-phone"/></svg>47382066</span>
    <span class="item" style="left:92px;gap:4px"><svg width="7" height="7"><use href="#icon-mail"/></svg>leif@fjordlast.no</span>
  </div>
  <div class="band band--red">
    <span class="item" style="left:13px;gap:4px"><svg width="7" height="7"><use href="#icon-pin"/></svg>8642 Raudvik</span>
  </div>
</section>

<!-- Sticker -->
<section class="sticker">
  <div class="wordmark">Kjelvraket</div>
  <div class="sticker-text sticker-line1">Fraktæ av Kjelvraket.</div>
  <div class="sticker-text sticker-line2">KE DU SYNS?</div>
  <div class="band band--red">Fjordlast.no/tilbakemelding</div>
  <div class="band band--navy">
    <span class="item" style="left:12px"><svg width="8" height="8"><use href="#icon-phone"/></svg>873 615 309</span>
  </div>
</section>

</body>
</html>
```